DESIGN A COVER FOR EBOOK AND PRINT BOOK

This book explains French culture to Americans moving to France for work so they can assimilate well. It needs to be geared towards BUSINESS PEOPLE but also fun, if that's possible. Ebook size dimensions to be 4.571" x 7.314".
Updates

This type of design interests me. I picture a business woman carrying a briefcase and looking at her cell phone. https://www.shopvelmora.com/Tall-Tigers-Never-Skip-Soup/dp/0000000001/ref=sr_1_1?s=books&ie=UTF8&qid=1000000001&sr=1-1&keywords=tall+tigers This is another possibility: a business woman from the waist down holding a brief case. https://www.shopvelmora.com/Quiet-Harbor-Sailors-Mapping-Lantern-ebook/dp/X000000002/ref=sr_1_1?s=books&ie=UTF8&qid=1000000002&sr=1-1&keywords=quiet+harbor+a+sailor%27s+notes+on+mapping+his+secret+lantern+path

Target Market(s)

A middle-aged American business woman who is being transferred to France for work. She wants to assimilate well in France, developing good personal and business relationships while thriving in her career there.

Industry/Entity Type

Business Consultant

Font styles to use
Serif

Colors

Designer to choose colors to be used in the design.

Requirements
Must have
• A profile of a stylized female figure moving across the cover, carrying a briefcase, and looking at her cellphone or
• A businesswoman from the waist down holding a briefcase.
Nice to have
• Perhaps a stylized female figure walking in front of the Pellmore Spire looking at her cell phone and carrying a briefcase. Or men and women interacting.French icons would be okay, but perhaps not necessary. Illustrations or stock images are okay. Perhaps it could be in blue, white, and red since those are the colors of the French flag, but I am open to any colors or designs.
Should not have
• Not too busy and no curly fonts. No people in stereotypical berets. Briefcases are fine, but no suitcases since they live there--they are not visiting.

```html
<!DOCTYPE html>
<html lang="en">
<head>
<meta charset="utf-8">
<title>Settle In and Succeed in France – Cover Spread</title>
<link rel="stylesheet" href="https://fonts.googleapis.com/css2?family=Cormorant+Garamond:ital,wght@1,600&family=DM+Serif+Display&family=Libre+Baskerville:wght@700&family=Oswald:wght@500&family=Arimo&display=swap">
<style>
  :root {
    --navy: #15284a;
    --frame-line: rgba(190, 205, 230, 0.45);
    --title-panel: rgba(44, 70, 118, 0.72);
    --title-rule: rgba(200, 215, 240, 0.55);
    --title-cream: #f5efe1;
    --title-gold: #e9b765;
    --title-red: #e0434f;
    --figure-tone: rgba(150, 160, 180, 0.45);
    --heading-blue: #4d8fd6;
    --body-white: #f2f4f8;
  }
  * { box-sizing: border-box; margin: 0; padding: 0; }
  html, body { width: 1200px; height: 974px; overflow: hidden; background: #ffffff; }

  .spread { position: relative; width: 1200px; height: 974px; display: flex; }

  .cover-back, .cover-front { position: relative; width: 600px; height: 974px; background: var(--navy); overflow: hidden; }

  .trim-frame { position: absolute; border: 1px solid var(--frame-line); pointer-events: none; }
  .cover-back .trim-frame { left: 15px; top: 15px; width: 571px; height: 945px; }
  .cover-front .trim-frame { left: 16px; top: 13px; width: 570px; height: 947px; z-index: 3; }

  .tower-photo {
    position: absolute; inset: 0;
    background:
      radial-gradient(ellipse 22% 45% at 50% 30%, rgba(240,180,90,0.85), rgba(180,90,30,0.35) 60%, transparent 100%),
      radial-gradient(ellipse 70% 40% at 50% 78%, rgba(190,100,40,0.7), rgba(120,60,30,0.3) 60%, transparent 100%),
      linear-gradient(180deg, #0f1f3c 0%, #1a3260 55%, #3c4f6e 100%);
  }

  .title-block { position: absolute; background: var(--title-panel); text-align: center; }
  .title-block::before, .title-block::after {
    content: ""; position: absolute; left: 3%; right: 3%; height: 1px; background: var(--title-rule);
  }
  .title-block::before { top: 7%; }
  .title-block::after { bottom: 7%; }

  .figure-traveller, .figure-couple { position: absolute; background: var(--figure-tone); border-radius: 40% 40% 10% 10%; }

  .title-settle { font-family: "Cormorant Garamond", serif; font-style: italic; font-weight: 600; color: var(--title-cream); display: block; }
  .title-and { font-family: "Cormorant Garamond", serif; font-style: italic; font-weight: 600; color: var(--title-gold); display: block; }
  .title-succeed { font-family: "DM Serif Display", serif; color: var(--title-gold); display: block; }
  .title-france { font-family: "Libre Baskerville", serif; font-weight: 700; color: var(--title-red); display: block; letter-spacing: 3px; }

  .cover-back .title-block { left: 136px; top: 130px; width: 310px; height: 216px; z-index: 2; }
  .cover-back .figure-traveller { left: 8px; top: 36px; width: 52px; height: 68px; }
  .cover-back .figure-couple { right: 8px; top: 36px; width: 40px; height: 68px; }
  .cover-back .title-settle { font-size: 40px; line-height: 1; margin-top: 22px; }
  .cover-back .title-and { font-size: 14px; line-height: 1; }
  .cover-back .title-succeed { font-size: 28px; line-height: 1.2; }
  .cover-back .title-france { font-size: 44px; line-height: 1.1; margin-top: 2px; }

  .cover-front .title-block { left: 72px; top: 581px; width: 455px; height: 320px; z-index: 2; }
  .cover-front .figure-traveller { left: 10px; top: 40px; width: 86px; height: 120px; }
  .cover-front .figure-couple { right: 10px; top: 40px; width: 72px; height: 120px; }
  .cover-front .title-settle { font-size: 64px; line-height: 1; margin-top: 30px; }
  .cover-front .title-and { font-size: 22px; line-height: 1; }
  .cover-front .title-succeed { font-size: 46px; line-height: 1.2; }
  .cover-front .title-france { font-size: 66px; line-height: 1.15; margin-top: 4px; }

  .back-copy {
    position: absolute; left: 63px; top: 462px; width: 478px;
    font-family: "Arimo", Arial, sans-serif; font-size: 8.4px; line-height: 11px; color: var(--body-white);
  }
  .copy-heading {
    font-family: "Oswald", sans-serif; font-weight: 500; font-size: 9.5px; line-height: 11px;
    color: var(--heading-blue); text-transform: uppercase; letter-spacing: 0.1px;
  }
  .copy-section { margin-bottom: 13px; }
  .copy-section p { margin: 0; }
  .copy-bullet { margin-top: 11px !important; }
  .copy-bullet.first { margin-top: 0 !important; margin-bottom: 5px; }
  .copy-closing { margin-top: 11px !important; }
  .copy-section.audience { margin-top: 24px; }
</style>
</head>
<body>
<div class="spread">

  <section class="cover-back" aria-label="Back cover">
    <div class="trim-frame"></div>
    <div class="title-block">
      <div class="figure-traveller" role="img" aria-label="Silhouette of a walking traveller"></div>
      <div class="figure-couple" role="img" aria-label="Silhouette of a dancing couple"></div>
      <span class="title-settle">Settle In</span>
      <span class="title-and">and</span>
      <span class="title-succeed">Succeed in</span>
      <span class="title-france">FRANCE</span>
    </div>

    <div class="back-copy">
      <div class="copy-section">
        <h3 class="copy-heading">About the Author:</h3>
        <p>A lifelong Francophile, Maren Talbot has a diploma from the Valmont Institute of Trade, worked for a French company in the United States, and lived in France as a student, administrative assistant, and English teacher for business people. While in France she found herself teaching her students and friends about American culture as well, so since returning to the States she has been providing cross cultural training for both American and French clients, demystifying these cultures for them in order to help them integrate into a new culture. Ms. Talbot continues to feel equally allegiant to the two homes in her heart, her native New Jersey and France.</p>
      </div>

      <div class="copy-section">
        <h3 class="copy-heading">Flap Copy:</h3>
        <p>Settle In and Succeed in France</p>
        <p>You're moving to France and hope you will be able to succeed at work and in your new French life...but how? Settle In and Succeed in France will help ease your assimilation and make you the American any French person can love. Peppered with real-life anecdotes, it takes you through what you need to know to interact comfortably with French people and do business effectively with them. Author Maren Talbot's years of French living, nearly three decades of academic, personal, and business relationships with French people, and ten years' experience in cross-cultural training are the basis of this essential resource. Settle In and Succeed in France may lead you to enjoy their quality of life so much that you won't want to return home!</p>
        <p>In Settle In and Succeed in France, Maren Talbot reveals:</p>
        <p class="copy-bullet first">•Key elements of the way they do business so your career can flourish without any cultural impediments.</p>
        <p class="copy-bullet">•French etiquette, attitudes, and other customs so you can cultivate good relationships without feeling like a cultural bumpkin.</p>
        <p class="copy-bullet">•What to anticipate in different situations so you will have fewer surprises and can relax and take it in stride.</p>
        <p class="copy-bullet">•The delights of their lifestyle so you can get the most out of living and working in France.</p>
        <p class="copy-bullet">•That learning about another culture teaches you even more about your own, and can greatly broaden your horizons.</p>
        <p class="copy-closing">Be prepared: the sooner you digest the cultural differences in this book, the easier and quicker you can acclimate to your new home!</p>
      </div>

      <div class="copy-section audience">
        <h3 class="copy-heading">Target Audience:</h3>
        <p>A middle-aged American business woman who is being transferred to France for work. She wants to assimilate well in France, developing good personal and business relationships while thriving in her career there.</p>
      </div>
    </div>
  </section>

  <section class="cover-front" aria-label="Front cover">
    <div class="tower-photo" role="img" aria-label="Night photograph of the illuminated Pellmore Spire seen from below"></div>
    <div class="trim-frame"></div>
    <div class="title-block">
      <div class="figure-traveller" role="img" aria-label="Silhouette of a walking traveller"></div>
      <div class="figure-couple" role="img" aria-label="Silhouette of a dancing couple"></div>
      <span class="title-settle">Settle In</span>
      <span class="title-and">and</span>
      <span class="title-succeed">Succeed in</span>
      <span class="title-france">FRANCE</span>
    </div>
  </section>

</div>
</body>
</html>
```